Calloway needs a modernized design

We would like a modern update (that can be responsive) to our existing website. Attached are the two existing pages we would like new concepts of - our home page and a page about one of our locations.

Calloway is provides executive offices and virtual office services. Startups, law firms, and financial services are our primary clients. We would like a professional, clean design, leaning towards minimalist. We intend to greatly reduce/eliminate the long paragraphs of text.

Requirements
Must have
• A design that can be responsive
Nice to have
• Large image(s) on home page that rotate.

```html
<!DOCTYPE html>
<html lang="en">
<head>
<meta charset="utf-8">
<title>Calloway Business Centers</title>
<link href="https://fonts.googleapis.com/css2?family=Lato:wght@400;700&family=Roboto:wght@400;500;700&family=Roboto+Condensed:wght@400;700&display=swap" rel="stylesheet">
<style>
:root{
  --navy:#2b3a6b;
  --navy-dark:#233059;
  --orange:#d4541a;
  --teal:#12b39d;
  --grey-bar:#dedede;
  --panel:#e9e9e9;
  --text:#222;
  --muted:#555;
  --btn:#dcdcdc;
  --white:#fff;
}
*{margin:0;padding:0;box-sizing:border-box}
html,body{width:764px;height:1200px;overflow:hidden;background:var(--white)}
body{position:relative;font-family:'Lato',sans-serif;color:var(--text)}
.abs{position:absolute}

/* header */
.brand{left:47px;top:13px;display:flex;align-items:center;gap:6px;color:var(--navy)}
.brand-dot{width:47px;height:47px;border-radius:50%;background:var(--navy)}
.brand-name{font-family:'Lato',serif;font-weight:400;line-height:1}
.brand-name .big{display:block;font-size:22px;letter-spacing:.3px}
.brand-name .small{display:block;font-size:9.5px;letter-spacing:1px;margin-top:3px}
.phone{top:27px;font-family:'Roboto',sans-serif;color:var(--navy)}
.phone .city{font-size:9px;font-weight:700;color:#555;display:block;letter-spacing:.4px}
.phone .num{font-size:13px;font-weight:700}
.social-top{left:595px;top:29px;display:flex;gap:3px}
.social-top span{width:22px;height:22px;border-radius:50%;background:#c8c8c8}

/* nav */
.nav{left:0;top:75px;width:764px;height:26px;background:var(--grey-bar)}
.nav a{position:absolute;top:7px;font-family:'Roboto',sans-serif;font-weight:700;font-size:11px;color:#444;text-decoration:none}

/* hero */
.hero{left:3px;top:101px;width:761px;height:326px;background:linear-gradient(120deg,#c9cdd2 0%,#e8eaec 40%,#b9bec4 70%,#8b9097 100%)}
.hero-tag{left:390px;top:221px;width:374px;height:69px;background:var(--navy);color:var(--white);font-family:'Roboto Condensed',sans-serif;font-weight:700;padding:9px 0 0 19px;line-height:1}
.hero-tag .l1{font-size:19px;display:block}
.hero-tag .l2{font-size:38px;display:block;margin-top:1px}

/* tabs */
.tabs{left:47px;top:430px;display:flex;gap:3px}
.tab{width:131.5px;height:50px;background:var(--navy);color:var(--white);font-family:'Roboto Condensed',sans-serif;font-size:14px;line-height:15px;padding:11px 0 0 11px}
.tab.active{background:var(--orange)}

/* intro */
.intro{left:46px;top:501px;width:450px;font-size:12.6px;line-height:17.6px;color:var(--text)}

/* features */
.feature{left:47px;width:441px;height:116px}
.feature-icon{position:absolute;left:0;top:0;width:86px;height:86px;border-radius:50%;background:var(--navy)}
.feature-icon svg{position:absolute;left:23px;top:23px}
.feature h2{position:absolute;left:114px;top:3px;font-family:'Lato',sans-serif;font-weight:700;font-size:12.5px;color:var(--navy)}
.feature p{position:absolute;left:114px;top:20px;width:330px;font-size:8.2px;line-height:15.4px;color:var(--muted)}
.feature .more{position:absolute;left:114px;top:71px;width:66px;height:21px;background:var(--btn);font-size:7.8px;color:#444;text-align:center;line-height:21px}
.divider{left:47px;width:441px;height:2px;background:#d6d6d6}

/* form */
.form{left:505px;top:504px;width:212px;height:406px;background:var(--panel)}
.form-head{position:absolute;left:0;top:0;width:212px;height:62px}
.form-head span{position:absolute;left:0;top:11px;width:212px;text-align:center;color:var(--white);font-family:'Roboto',sans-serif;font-weight:700;font-size:13px;line-height:15px}
.field-label{position:absolute;left:12px;font-size:8.3px;color:#444}
.field{position:absolute;left:12px;width:188px;height:24px;background:var(--white);border:1px solid #ddd;font-size:8.5px;color:#333;padding:7px 0 0 7px}
.field .caret{position:absolute;right:8px;top:8px}
.submit{position:absolute;left:12px;top:369px;width:71px;height:24px;background:var(--orange);color:var(--white);font-family:'Roboto',sans-serif;font-weight:700;font-size:8.5px;text-align:center;line-height:24px}

/* footer */
.footer{left:0;top:937px;width:764px;height:235px;background:var(--navy);color:var(--white)}
.footer h3{position:absolute;top:33px;font-family:'Roboto',sans-serif;font-weight:700;font-size:10.5px}
.links{position:absolute;left:38px;top:55px;font-size:8.5px;line-height:15.4px;list-style:none}
.contact{position:absolute;left:161px;top:56px;font-size:8.5px;line-height:15.4px}
.contact .big{font-size:11.5px;line-height:12px}
.social-foot{position:absolute;left:310px;top:54px;display:flex;gap:4px}
.social-foot span{width:23px;height:23px;border-radius:50%;background:var(--white)}
.seal{position:absolute;left:315px;top:101px}
.specials{position:absolute;left:505px;top:25px;width:212px;height:155px;background:linear-gradient(160deg,#dfe7ef 0%,#8fa9c4 45%,#34547c 100%)}
.specials .frame{position:absolute;left:8px;top:8px;right:8px;bottom:8px;border:1px solid rgba(255,255,255,.7)}
.specials .label{position:absolute;left:0;top:63px;width:212px;text-align:center;font-family:'Roboto Condensed',sans-serif;color:var(--white);line-height:1}
.specials .label .s{font-size:11px;display:block}
.specials .label .b{font-size:20px;display:block;margin-top:1px;letter-spacing:.5px}
.copy{left:0;top:1172px;width:764px;height:28px;background:var(--navy-dark);color:var(--white);font-size:8.5px;text-align:center;line-height:28px}
</style>
</head>
<body>

<header>
  <div class="abs brand">
    <span class="brand-dot"></span>
    <span class="brand-name"><span class="big">CALLOWAY</span><span class="small">BUSINESS CENTERS</span></span>
  </div>
  <div class="abs phone" style="left:398px"><span class="city">DALLAS</span><span class="num">214.555.0140</span></div>
  <div class="abs phone" style="left:498px"><span class="city">HOUSTON</span><span class="num">713.555.0186</span></div>
  <div class="abs social-top"><span></span><span></span><span></span><span></span><span></span></div>
</header>

<nav class="abs nav">
  <a style="left:132px">HOME</a>
  <a style="left:198px">PROPERTIES</a>
  <a style="left:294px">VIRTUAL TOURS &amp; VIDEOS</a>
  <a style="left:456px">PHOTOS</a>
  <a style="left:534px">BROKER REFERRALS</a>
</nav>

<div class="abs hero" role="img" aria-label="Photo of a business team gathered around a laptop in a bright office"></div>
<div class="abs hero-tag"><span class="l1">EXECUTIVE OFFICE SOLUTIONS.</span><span class="l2">ONE LOW COST.</span></div>

<div class="abs tabs">
  <div class="tab active">EXECUTIVE OFFICE<br>SUITES</div>
  <div class="tab">ONDEMAND<br>MEETING ROOMS</div>
  <div class="tab">ONDEMAND<br>TRAINING ROOMS</div>
  <div class="tab">VIRTUAL OFFICE<br>SOLUTIONS</div>
  <div class="tab">VIDEO CONFERENCE<br>SOLUTIONS</div>
</div>

<p class="abs intro">Come See Why Smarter Companies are Choosing Calloway Business Centers' Dallas, Ft. Worth and Houston Executive Office Suites, Virtual Offices, Meeting Rooms and Video Conferencing.</p>

<section class="abs feature" style="top:583px">
  <div class="feature-icon"><svg width="40" height="40" viewBox="0 0 40 40" fill="none" stroke="#fff" stroke-width="2.4" stroke-linejoin="round"><path d="M9 8h22l6 9-17 18L3 17z"/><path d="M3 17h34M15 8l-4 9 9 18 9-18-4-9"/></svg></div>
  <h2>VALUE</h2>
  <p>Either you need Dallas/Ft. Worth Office Space, Dallas Executive Suites, Ft. Worth Executive Suites, Houston Office Space, Houston Executive Suites, or maybe you simply need a place to stop in and use an on-demand office or meeting room...</p>
  <div class="more">READ MORE</div>
</section>
<div class="abs divider" style="top:685px"></div>

<section class="abs feature" style="top:699px">
  <div class="feature-icon"><svg width="40" height="40" viewBox="0 0 40 40" fill="#fff"><circle cx="20" cy="9" r="5"/><circle cx="8" cy="15" r="4"/><circle cx="32" cy="15" r="4"/><path d="M13 30c0-8 14-8 14 0v2H13z"/><path d="M2 28c0-6 9-7 10-3v5H2z"/><path d="M38 28c0-6-9-7-10-3v5h10z"/><path d="M6 33c6 5 22 5 28 0" stroke="#fff" stroke-width="2" fill="none"/></svg></div>
  <h2>COMMUNITY</h2>
  <p>Companies that partner with Calloway share more than a prestigious address. They also share ideas and services. Our Executive Office Business Centers are places where savvy, growing companies can network, interact and learn from one...</p>
  <div class="more">READ MORE</div>
</section>
<div class="abs divider" style="top:801px"></div>

<section class="abs feature" style="top:815px">
  <div class="feature-icon"><svg width="40" height="40" viewBox="0 0 40 40"><g fill="#fff"><circle cx="20" cy="20" r="13"/><g id="t"><rect x="17" y="2" width="6" height="8"/></g><use href="#t" transform="rotate(45 20 20)"/><use href="#t" transform="rotate(90 20 20)"/><use href="#t" transform="rotate(135 20 20)"/><use href="#t" transform="rotate(180 20 20)"/><use href="#t" transform="rotate(225 20 20)"/><use href="#t" transform="rotate(270 20 20)"/><use href="#t" transform="rotate(315 20 20)"/></g><circle cx="20" cy="20" r="7" fill="#2b3a6b"/><path d="M14 27l10-10" stroke="#fff" stroke-width="3" stroke-linecap="round"/></svg></div>
  <h2>SERVICE</h2>
  <p>Calloway Business Centers positions its management team in every one of its business centers we operate with an opendoor policy as a mediumsized company without all of the corporate bureaucracy and red tape...</p>
  <div class="more">READ MORE</div>
</section>

<aside class="abs form">
  <svg class="form-head" width="212" height="62" viewBox="0 0 212 62"><path d="M0 0h212v44l-106 18L0 44z" fill="#12b39d"/></svg>
  <div class="form-head"><span>REQUEST<br>INFORMATION</span></div>
  <span class="field-label" style="top:79px">First Name</span><div class="field" style="top:92px"></div>
  <span class="field-label" style="top:127px">Last Name</span><div class="field" style="top:140px"></div>
  <span class="field-label" style="top:175px">Phone Number</span><div class="field" style="top:188px"></div>
  <span class="field-label" style="top:223px">Email</span><div class="field" style="top:237px"></div>
  <span class="field-label" style="top:272px">Property Interested In:</span><div class="field" style="top:285px"><svg class="caret" width="10" height="8"><path d="M0 0h10L5 8z" fill="#555"/></svg></div>
  <span class="field-label" style="top:320px">Product Interested In:</span><div class="field" style="top:333px">Executive Offices<svg class="caret" width="10" height="8"><path d="M0 0h10L5 8z" fill="#555"/></svg></div>
  <div class="submit">SUBMIT</div>
</aside>

<footer class="abs footer">
  <h3 style="left:38px">QUICK LINKS</h3>
  <ul class="links"><li>About Us</li><li>Contact Us</li><li>Forms</li><li>Testimonials</li><li>FAQs</li><li>Careers</li><li>Furniture</li><li>Specials</li><li>Site Map</li><li>Privacy</li></ul>
  <h3 style="left:161px">CONTACT US</h3>
  <div class="contact">Calloway Business Centers<br>4120 Lakeview Parkway<br>Suite 300<br>Dallas, Texas 75204<br><br>Dallas<br><span class="big">214.555.0140</span><br><br>Houston<br><span class="big">713.555.0186</span></div>
  <h3 style="left:311px">FOLLOW US</h3>
  <div class="social-foot"><span></span><span></span><span></span><span></span><span></span></div>
  <svg class="seal" width="100" height="88" viewBox="0 0 100 88"><circle cx="50" cy="44" r="42" fill="#c9ccd3"/><circle cx="50" cy="44" r="30" fill="#2b3a6b"/></svg>
  <div class="specials" role="img" aria-label="Photo looking up at glass office towers">
    <div class="frame"></div>
    <div class="label"><span class="s">VIEW</span><span class="b">CURRENT SPECIALS</span></div>
  </div>
</footer>
<div class="abs copy">Copyright 2016 Calloway Business Centers All Rights Reserved</div>

</body>
</html>
```